Tarn Workforce Tri Fold Brochure

My company is a recruiting/staffing firm. I need a design that is going to be professional, bright, young, hip and fun. Pictures are key! We want people working in an office, packaging, food production and/or light industrial environment. Must embrace DIVERSITY. Please use the 4 primary colors from the Tarn Logo to accent the piece, but not too busy. I am including the content that I would like to be included in the trifold as well as a sample of a trifold I have used in the past in addition to a couple of logos. My website is www.TarnWorkforce-example.com for look and feel.

Target Market(s)

Logistics, Distribution and Manufacturing companies

Industry/Entity Type

Staffing

Requirements
Must have
• Clean, colorful, eye catching, great pictures and graphics. Photo's of diverse people working, in a office, or production setting.
Nice to have
• Must be professional
Should not have
• Not too busy.

```html
<!DOCTYPE html>
<html lang="en">
<head>
<meta charset="utf-8">
<title>Tarn Workforce Tri-Fold Brochure</title>
<link href="https://fonts.googleapis.com/css2?family=Open+Sans:wght@400;600;700;800&display=swap" rel="stylesheet">
<style>
:root{
  --red:#e2372b;
  --green:#3ba44a;
  --yellow:#f5c02a;
  --blue:#1e8bcf;
  --ink:#3a3a3a;
  --muted:#777;
  --paper:#ffffff;
  --stage:#f1f1f1;
}
*{margin:0;padding:0;box-sizing:border-box}
html,body{width:672px;height:1200px;overflow:hidden}
body{background:var(--stage);font-family:"Open Sans",Arial,sans-serif;color:var(--ink);position:relative}
.spread{position:absolute;left:36px;width:600px;height:464px;background:var(--paper);display:flex;box-shadow:0 2px 8px rgba(0,0,0,.12)}
.spread.outside{top:116px}
.spread.inside{top:620px}
.panel{position:relative;width:200px;height:100%;overflow:hidden}
.photo{position:absolute}
.brand{font-weight:800;font-size:26px;color:var(--ink);display:flex;align-items:center;gap:5px;letter-spacing:.5px}
.brand .dot{width:8px;height:8px;border-radius:50%;background:var(--red)}
/* outside left */
.quote-mark{position:absolute;font-size:44px;font-weight:800;color:#c9c9c9;line-height:1}
.tagline{position:absolute;left:34px;top:34px;width:142px;font-size:11.5px;line-height:1.35;color:var(--ink)}
.tagline b{font-weight:800}
/* contact panel */
.contact .brand{position:absolute;left:62px;top:14px}
.contact-tab{position:absolute;left:48px;top:58px;width:104px;height:16px;background:var(--yellow);color:var(--red);font-size:7.5px;font-weight:800;text-align:center;line-height:16px;letter-spacing:.6px}
.offices{position:absolute;left:0;top:74px;width:200px;height:176px;background:var(--red);color:#fff;text-align:center;padding-top:10px}
.office{margin-bottom:9px}
.office h4{font-size:7px;font-weight:700;margin-bottom:2px;letter-spacing:.4px}
.office p{font-size:6px;line-height:1.45}
.hotline{position:absolute;top:268px;left:0;width:200px;text-align:center}
.hotline .phone{display:inline-flex;align-items:center;gap:5px;font-size:15px;font-weight:800;color:var(--ink)}
.hotline .addr{font-size:6.5px;color:var(--muted);margin-top:6px;line-height:1.5}
.hotline .or{font-size:6px;color:var(--muted);margin:6px 0}
.hotline .web{font-size:7px;font-weight:700;color:var(--blue)}
/* cover */
.cover .brand{position:absolute;right:18px;top:14px}
.slogan{position:absolute;left:0;top:300px;width:200px;height:78px;background:var(--green);color:#fff;padding:12px 16px;font-weight:800;line-height:1.1}
.slogan .l1{font-size:15px}
.slogan .l2{font-size:10px}
.slogan .l3{font-size:17px;color:var(--yellow)}
.cover .web{position:absolute;bottom:22px;right:18px;font-size:7px;color:var(--muted)}
/* inside */
.copy{padding:18px 16px}
.head{font-size:7.5px;font-weight:800;color:var(--red);letter-spacing:.4px;margin-bottom:5px;text-transform:uppercase}
.body{font-size:5.6px;line-height:1.55;color:#555;margin-bottom:9px}
.rule{height:1px;background:#e3e3e3;margin:6px 0 9px}
.option{display:flex;gap:7px;margin-bottom:10px}
.icon{flex:0 0 16px;height:16px;border-radius:50%;display:flex;align-items:center;justify-content:center}
.option h5{font-size:7px;font-weight:700;color:var(--ink);margin-bottom:3px}
.option .body{margin-bottom:0}
.sector{display:flex;gap:7px;margin-bottom:9px}
.sector h5{font-size:7px;font-weight:700;color:var(--ink);margin-bottom:3px}
.sector ul{list-style:none;columns:2;column-gap:10px;font-size:5.6px;line-height:1.6;color:#555}
.sector li::before{content:"• ";color:var(--green)}
</style>
</head>
<body>

<!-- Outside spread -->
<section class="spread outside">
  <div class="panel pitch">
    <span class="quote-mark" style="left:12px;top:14px">“</span>
    <p class="tagline"><b>YES</b> the <b>CANDIDATE</b> meets the requirements, <b>YEAH</b> they <b>HAVE</b> the skills, but do they <b>TARN?</b></p>
    <span class="quote-mark" style="left:150px;top:104px">”</span>
    <div class="photo" role="img" aria-label="Photo of a smiling professional woman holding a tablet in a bright office"
         style="left:0;top:150px;width:200px;height:314px;background:linear-gradient(160deg,#eef0f2,#cdd2d6 60%,#b9bfc4)"></div>
  </div>

  <div class="panel contact">
    <div class="brand"><span class="dot"></span>Tarn</div>
    <div class="contact-tab">CONTACT US</div>
    <div class="offices">
      <div class="office"><h4>CORPORATE</h4><p>Main Office – 555-014-2290<br>Payroll – 555-014-2291</p></div>
      <div class="office"><h4>NORTH BRANCH</h4><p>Office – 555-014-3310<br>Recruiting – 555-014-3311</p></div>
      <div class="office"><h4>RIVERSIDE</h4><p>Office – 555-014-4420</p></div>
      <div class="office"><h4>WESTGATE</h4><p>Office – 555-014-5530<br>Recruiting – 555-014-5531</p></div>
      <div class="office"><h4>EASTFIELD</h4><p>Office – 555-014-6640</p></div>
    </div>
    <div class="hotline">
      <div class="phone">
        <svg width="13" height="13" viewBox="0 0 24 24"><path fill="#e2372b" d="M6.6 10.8a15 15 0 0 0 6.6 6.6l2.2-2.2c.3-.3.7-.4 1-.2 1.1.4 2.3.6 3.6.6.6 0 1 .4 1 1V20c0 .6-.4 1-1 1A17 17 0 0 1 3 4c0-.6.4-1 1-1h3.5c.6 0 1 .4 1 1 0 1.3.2 2.5.6 3.6.1.3 0 .7-.2 1z"/></svg>
        555-014-2290
      </div>
      <p class="addr">240 Harbor Lane, Suite 12<br>Millbrook, GA 30000</p>
      <p class="or">or</p>
      <p class="web">www.TarnWorkforce-example.com</p>
    </div>
  </div>

  <div class="panel cover">
    <div class="brand"><span class="dot"></span>Tarn</div>
    <div class="photo" role="img" aria-label="Photo of two technicians working together at a computer workstation"
         style="left:0;top:60px;width:200px;height:240px;background:linear-gradient(135deg,#4f6475,#8da0ad 55%,#c9d2d8)"></div>
    <div class="slogan">
      <div class="l1">CONNECTING</div>
      <div class="l2">GREAT PEOPLE WITH</div>
      <div class="l3">GREAT JOBS</div>
    </div>
    <p class="web">www.TarnWorkforce-example.com</p>
  </div>
</section>

<!-- Inside spread -->
<section class="spread inside">
  <div class="panel copy">
    <h3 class="head">Definition of “Tarn” – noun</h3>
    <p class="body">1. To fit together in harmony; to agree or match. 2. To be a natural fit between the right person and the right role.</p>
    <h3 class="head">Synonyms</h3>
    <p class="body">Fit, match, suit, agree, align, connect, blend, belong.</p>
    <div class="rule"></div>
    <h3 class="head">Who We Are</h3>
    <p class="body">Tarn Workforce is a locally owned staffing firm serving logistics, distribution and manufacturing companies. Our team brings years of hiring experience and a genuine care for the people we place.</p>
    <p class="body">We believe great work starts with the right fit. Skills matter, but so do attitude, reliability and culture. That is why we take time to know every client and every candidate.</p>
    <h3 class="head">What We Do</h3>
    <p class="body">We recruit, screen and place dependable workers for short term needs, seasonal peaks and long term growth. Every candidate is interviewed, reference checked and matched to your goals.</p>
    <p class="body">From a single hire to a full shift, we move quickly so your floor keeps running and your people keep growing.</p>
  </div>

  <div class="panel copy">
    <h3 class="head">Staffing Options</h3>
    <div class="option">
      <span class="icon" style="background:var(--red)"><svg width="9" height="9" viewBox="0 0 24 24"><circle cx="12" cy="12" r="9" fill="none" stroke="#fff" stroke-width="3"/><path d="M12 7v5l3 3" stroke="#fff" stroke-width="3" fill="none"/></svg></span>
      <div><h5>Temporary</h5><p class="body">Flexible workers for busy seasons, special projects or absences, ready when you need them.</p></div>
    </div>
    <div class="option">
      <span class="icon" style="background:var(--green)"><svg width="9" height="9" viewBox="0 0 24 24"><path d="M4 12h13M12 6l6 6-6 6" stroke="#fff" stroke-width="3" fill="none"/></svg></span>
      <div><h5>Temp-to-Hire</h5><p class="body">Try before you commit. Evaluate fit on the job, then hire with full confidence.</p></div>
    </div>
    <div class="option">
      <span class="icon" style="background:var(--blue)"><svg width="9" height="9" viewBox="0 0 24 24"><path d="M4 12l5 5 11-11" stroke="#fff" stroke-width="3" fill="none"/></svg></span>
      <div><h5>Direct Hire</h5><p class="body">We search and screen for permanent team members who match your skills and culture.</p></div>
    </div>
    <div class="photo" role="img" aria-label="Photo of a welder at work with bright orange sparks in a factory"
         style="left:0;top:300px;width:400px;height:164px;background:linear-gradient(120deg,#2b2522,#6a3a1c 45%,#e88a2a 70%,#3a2c24)"></div>
  </div>

  <div class="panel copy">
    <h3 class="head">Growth Management</h3>
    <p class="body">We help you plan for growth by building a steady pipeline of trained, reliable workers across every shift.</p>
    <div class="sector">
      <span class="icon" style="background:var(--red)"><svg width="9" height="9" viewBox="0 0 24 24"><rect x="4" y="8" width="16" height="12" fill="#fff"/></svg></span>
      <div><h5>Light Industrial</h5><ul><li>Assembly</li><li>Packaging</li><li>Forklift</li><li>Shipping</li></ul></div>
    </div>
    <div class="sector">
      <span class="icon" style="background:var(--green)"><svg width="9" height="9" viewBox="0 0 24 24"><rect x="5" y="4" width="14" height="16" fill="#fff"/></svg></span>
      <div><h5>Clerical</h5><ul><li>Reception</li><li>Data Entry</li><li>Billing</li><li>Admin</li></ul></div>
    </div>
    <div class="sector">
      <span class="icon" style="background:var(--blue)"><svg width="9" height="9" viewBox="0 0 24 24"><circle cx="12" cy="12" r="7" fill="#fff"/></svg></span>
      <div><h5>Skilled Trades</h5><ul><li>Welding</li><li>Maintenance</li><li>Electrical</li><li>Machining</li></ul></div>
    </div>
  </div>
</section>

</body>
</html>
```